Envelope Design Project

I will need two envelopes to be designed:-

DL size
C4 size

Please see uploaded documents for Design specs:

1) Design specs provided by printer (doc called DL Envelope Specs)
2) Design specs to comply with Kestrel Courier requirements (doc called Kestrel Courier Envelope Design Requirements)

Please adhere to the above for final design. Many thanks.

Target Market(s)

Real Estate Agents, Strata Managers, Builders, Architects, Business Owners

Industry/Entity Type

Printer

Requirements
Must have
• In top left corner
- Logo
- Return address - Suite 6, 19 Marlowe St, Linden Cove, NSW 2999

```html
<!DOCTYPE html>
<html lang="en">
<head>
<meta charset="utf-8">
<title>Corvane Asbestos &amp; Safety – Stationery</title>
<link href="https://fonts.googleapis.com/css2?family=Questrial&family=Arimo:wght@400&display=swap" rel="stylesheet">
<style>
  :root{
    --bg:#dcdcdc;
    --paper:#ffffff;
    --navy:#222b4b;
    --green:#8bbd3b;
    --grey-text:#6d6d6d;
    --body-text:#1e1e1e;
    --swatch:#717171;
  }
  *{margin:0;padding:0;box-sizing:border-box}
  html,body{width:1200px;height:829px;overflow:hidden;background:var(--bg)}
  .canvas{position:relative;width:1200px;height:829px;background:var(--bg);font-family:"Questrial",sans-serif}
  .shapes{position:absolute;left:0;top:0}
  .brand{position:absolute;display:flex;flex-direction:column;line-height:1}
  .brand-row{display:flex;align-items:center;gap:5px}
  .brand-square{background:var(--navy);border-radius:4px}
  .brand-name{color:var(--green);font-family:"Questrial",sans-serif;font-weight:400}
  .brand-tag{color:var(--navy);font-family:"Questrial",sans-serif;letter-spacing:.2px}
  .return-address{position:absolute;color:var(--grey-text);font-family:"Arimo",sans-serif;line-height:1.25}
  .letter-body{position:absolute;left:98px;top:233px;width:284px;font-family:"Arimo",sans-serif;font-size:7.6px;line-height:9.1px;color:var(--body-text)}
  .letter-body p{margin-bottom:9.1px}
  .signature{position:absolute;left:94px;top:460px;width:98px;height:20px;background:linear-gradient(90deg,rgba(31,63,176,.25),rgba(31,63,176,.08));border-radius:3px}
  .signatory-role{position:absolute;left:98px;top:483px;font-family:"Arimo",sans-serif;font-size:7.5px;color:var(--body-text)}
  .letter-contact{position:absolute;left:79px;top:564px;display:flex;gap:5px;font-family:"Arimo",sans-serif;font-size:5.6px;line-height:8px;color:var(--grey-text)}
  .letter-contact .col{padding-right:4px;border-right:.6px solid var(--green)}
  .letter-contact .col:last-child{border-right:none}
  .letter-contact b{color:var(--green);font-weight:400;margin-right:3px}
  .acn{position:absolute;left:80px;top:591px;font-family:"Arimo",sans-serif;font-size:5.6px;color:#fff}
  .swatch{position:absolute;left:935px;top:616px;width:220px;height:161px;background:var(--swatch)}
  .swatch-label{position:absolute;left:35px;top:58px;font-family:"Questrial",sans-serif;font-size:35px;line-height:44px;color:#1f1f1f}
</style>
</head>
<body>
<div class="canvas">
  <svg class="shapes" width="1200" height="829" viewBox="0 0 1200 829">
    <rect x="42" y="47" width="394" height="558" fill="var(--paper)"/>
    <rect x="42" y="585" width="394" height="20" fill="var(--navy)"/>
    <polygon points="294,577 436,577 436,605 276,605" fill="var(--green)"/>
    <polygon points="278,605 294,577 297,577 281,605" fill="var(--paper)"/>
    <path d="M1070,47 L1128,57 Q1138,60 1139,70 L1155,262 L1139,455 Q1138,465 1128,467 L1070,477 Z" fill="var(--paper)"/>
    <rect x="462" y="47" width="608" height="430" fill="var(--paper)"/>
    <line x1="1070" y1="47" x2="1070" y2="477" stroke="#e6e6e6" stroke-width="1"/>
    <rect x="462" y="457" width="458" height="20" fill="var(--navy)"/>
    <polygon points="926,449 1070,449 1070,477 910,477" fill="var(--green)"/>
    <path d="M462,570 L470,520 Q473,507 488,507 L848,507 Q863,507 866,520 L875,570 Z" fill="var(--paper)"/>
    <rect x="462" y="570" width="413" height="207" fill="var(--paper)"/>
    <line x1="462" y1="570" x2="875" y2="570" stroke="#e6e6e6" stroke-width="1"/>
    <rect x="462" y="758" width="262" height="19" fill="var(--navy)"/>
    <polygon points="730,749 875,749 875,777 714,777" fill="var(--green)"/>
  </svg>

  <div class="brand" style="left:80px;top:86px">
    <div class="brand-row">
      <span class="brand-square" style="width:20px;height:20px"></span>
      <span class="brand-name" style="font-size:25px">Corvane</span>
    </div>
    <span class="brand-tag" style="font-size:10px;margin-top:6px;margin-left:3px">ASBESTOS &amp; SAFETY</span>
  </div>

  <div class="letter-body">
    <p>Letterhead samples are a great way of deciding what kind of letterhead you want to design for you and your company. The internet has a ton of great letterhead samples to browse through. Whether you want something simple, with just a couple lines of text of your business information, or something decorative and stunning, with photos and logos on the top and bottom of the page, it will be easy to find what you want, because there are samples online for basically any type of letterhead you could want.</p>
    <p>Any business could easily benefit from browsing through some letterhead samples, if only to get an idea for what kind of letterhead their company might want. Letterheads are just one of the tools that a business professional could use to help increase their customer base, and to really be memorable to everyone they write a letter to. Letterhead is quite an effective tool for marketing and advertising, but because it’s such a simple and well known idea, it is often unfairly overlooked. Make sure you don’t make that mistake, and make some letterhead samples of your own today.</p>
    <p>Whether you want to get new customers to remember you and become part of your clientele, or you just want to send out friendly reminders to your existing clients, customizing your own letterhead samples can really help you out. Try out some letterhead samples and you will not regret it, and I’m sure you will add a new tool to your business’ arsenal of networking, marketing, and advertising tools.</p>
  </div>
  <div class="signature" role="img" aria-label="Handwritten signature of Harriet Oakley"></div>
  <div class="signatory-role">company director</div>

  <div class="letter-contact">
    <div class="col"><b>P</b>(02) 5550 1234<br><b>F</b>(02) 5550 5678</div>
    <div class="col">Suite 6, 19 Marlowe St<br>Linden Cove, NSW 2999</div>
    <div class="col">info@corvanesafety.example<br>www.corvanesafety.example</div>
  </div>
  <div class="acn">ACN - 000 111 222</div>

  <div class="brand" style="left:503px;top:96px">
    <div class="brand-row">
      <span class="brand-square" style="width:24px;height:24px"></span>
      <span class="brand-name" style="font-size:28px">Corvane</span>
    </div>
    <span class="brand-tag" style="font-size:10.5px;margin-top:6px;margin-left:3px">ASBESTOS &amp; SAFETY</span>
  </div>
  <div class="return-address" style="left:507px;top:154px;font-size:9.3px">Suite 6, 19 Marlowe St<br>Linden Cove, NSW 2999</div>

  <div class="brand" style="left:490px;top:600px">
    <div class="brand-row">
      <span class="brand-square" style="width:15px;height:15px;border-radius:3px"></span>
      <span class="brand-name" style="font-size:18px">Corvane</span>
    </div>
    <span class="brand-tag" style="font-size:7.3px;margin-top:4px;margin-left:2px">ASBESTOS &amp; SAFETY</span>
  </div>
  <div class="return-address" style="left:492px;top:636px;font-size:6.4px">Suite 6, 19 Marlowe St<br>Linden Cove, NSW 2999</div>

  <div class="swatch"><div class="swatch-label">address<br>color</div></div>
</div>
</body>
</html>
```